Business cards to launch an education platform

Hi,
I am looking at having new business cards designed.
I am a startup, developing a web platform for schools and university, the education world. It's an online assessment system.
I would like a card that looks classy, and that is using the colors and the font of my logo.

I have attached:
1) my logo
2) A business card that I have designed quickly so you can have all the information required in the card, but I really don't like it.
3) The font that I am using (Lato Regular) to design my web platform
4) Some screenshots of my web platform so you can have a look at the style that I have.

Target Market(s)

Major market: Education system: Schools and university
Minor markets: Business in general

Industry/Entity Type

Business

Contact Information for Business Card

Clara Fenwick
Director

M: 0437 518 902
E: clara.fenwick@amberLoomSystems.com.au

Requirements
Must have
• The colors of my logo

```html
<!DOCTYPE html>
<html lang="en">
<head>
<meta charset="utf-8">
<title>Amber Loom Systems – Business Cards</title>
<link href="https://fonts.googleapis.com/css2?family=Lato:wght@400;700&display=swap" rel="stylesheet">
<style>
  :root {
    --page-bg: #e9e7e3;
    --brand-navy: #0f4a7c;
    --brand-blue: #1f5a8c;
    --brand-sky: #2fa9e0;
    --card-white: #ffffff;
    --text-grey: #55595e;
    --shadow: rgba(0, 0, 0, 0.18);
  }
  * { box-sizing: border-box; margin: 0; padding: 0; }
  html, body {
    width: 1200px;
    height: 950px;
    overflow: hidden;
    background: var(--page-bg);
    font-family: "Lato", Arial, sans-serif;
  }
  .sheet {
    position: relative;
    width: 1200px;
    height: 950px;
  }
  .card {
    position: absolute;
    left: 250px;
    width: 700px;
    height: 400px;
    box-shadow: 0 10px 30px var(--shadow);
  }
  /* Back of card */
  .card--back {
    top: 50px;
    background: var(--brand-navy);
    color: var(--card-white);
  }
  .back-brand {
    position: absolute;
    top: 120px;
    left: 0;
    right: 0;
    display: flex;
    align-items: center;
    justify-content: center;
    gap: 16px;
  }
  .back-brand .brand-square {
    width: 44px;
    height: 44px;
    background: var(--card-white);
  }
  .back-brand .brand-name {
    font-size: 38px;
    font-weight: 400;
    letter-spacing: 2px;
    color: var(--card-white);
  }
  .back-website {
    position: absolute;
    bottom: 70px;
    left: 0;
    right: 0;
    text-align: center;
    font-size: 18px;
    letter-spacing: 3px;
    color: var(--card-white);
  }
  /* Front of card */
  .card--front {
    top: 500px;
    background: var(--card-white);
  }
  .front-brand {
    position: absolute;
    top: 48px;
    right: 44px;
    display: flex;
    align-items: center;
    gap: 12px;
  }
  .front-brand .brand-square {
    width: 34px;
    height: 34px;
    background: var(--brand-sky);
  }
  .front-brand .brand-name {
    font-size: 28px;
    font-weight: 400;
    letter-spacing: 1.5px;
    color: var(--brand-blue);
  }
  .accent-bar {
    position: absolute;
    left: 0;
    bottom: 40px;
    width: 10px;
    height: 130px;
    background: var(--brand-navy);
  }
  .contact {
    position: absolute;
    left: 56px;
    bottom: 40px;
  }
  .contact-name {
    font-size: 26px;
    font-weight: 700;
    color: var(--brand-navy);
  }
  .contact-title {
    font-size: 18px;
    font-weight: 400;
    color: var(--brand-sky);
    margin-top: 2px;
    margin-bottom: 22px;
  }
  .contact-line {
    display: flex;
    align-items: center;
    gap: 12px;
    font-size: 17px;
    color: var(--text-grey);
    margin-top: 6px;
  }
  .contact-line svg { flex: none; }
</style>
</head>
<body>
  <main class="sheet">
    <section class="card card--back" aria-label="Card back">
      <div class="back-brand">
        <span class="brand-square"></span>
        <span class="brand-name">Amber Loom Systems</span>
      </div>
      <p class="back-website">www.amberLoomSystems.com.au</p>
    </section>

    <section class="card card--front" aria-label="Card front">
      <div class="front-brand">
        <span class="brand-square"></span>
        <span class="brand-name">Amber Loom Systems</span>
      </div>

      <span class="accent-bar"></span>

      <div class="contact">
        <p class="contact-name">Clara Fenwick</p>
        <p class="contact-title">Director</p>
        <p class="contact-line">
          <svg width="14" height="22" viewBox="0 0 14 22" aria-hidden="true">
            <rect x="1" y="1" width="12" height="20" rx="2" fill="none" stroke="#0f4a7c" stroke-width="2"/>
            <rect x="3.5" y="4" width="7" height="11" fill="#0f4a7c"/>
            <circle cx="7" cy="18" r="1.2" fill="#0f4a7c"/>
          </svg>
          <span>0437 518 902</span>
        </p>
        <p class="contact-line">
          <svg width="18" height="14" viewBox="0 0 18 14" aria-hidden="true">
            <rect x="0" y="0" width="18" height="14" fill="#0f4a7c"/>
            <path d="M1 1 L9 8 L17 1" fill="none" stroke="#ffffff" stroke-width="1.5"/>
          </svg>
          <span>clara.fenwick@amberLoomSystems.com.au</span>
        </p>
      </div>
    </section>
  </main>
</body>
</html>
```